Hollow Meridian Book website design.

This is a simple one-page web design for my book.
I have all files and video needed.
Domain listed with Net Harbor.
Password and username will be given to winning bid.
Domain address, www.hollowmeridian.info
Upload a 30 second video so it can be played on the website.
Book cover photo
Book Blurb text.
Links to Rivermart and Audio books where the book can be purchased.
Below is the link to the Rivermart listing.
https://www.rivermart.example/dp/X00AAAAAA1/?coliid=QWERTYUIOPASD&colid=1ZXCVBNMLKJH0&psc=0&ref_=lv_ov_lig_dp_i
Below is the link to my Listenly books.com listing.
https://www.listenly.example/pd/Hollow-Meridian-Audiobook/X00BBBBBB2?qid=1000000001&sr=1-7&ref=a_search_c3_lProduct_1_7&pf_rd_p=00000000-aaaa-bbbb-cccc-000000000000&pf_rd_r=ZZZZ00000000000000QQ
Text on page.” Click on either logo to go directly to Rivermart or Listenly.com
Link Listenly book logo to my book on Listenly.com
Place this text under Listenly.com logo: “Free to new members of Listenly.com”
Link Rivermart logo to my book on Rivermart.
Place this text under Rivermart logo “ Free to new Pagewisp members on Rivermart.com”
Link the book photo to the Rivermart.com web address as well.
Enter meta tags or keywords below for search engines to locate webpage.
Hollow Meridian
Conspiracy
Conspiracy Books
Spy books
Thriller books
Suspense books
Comedy books
Dorian Welbeck

```html
<!DOCTYPE html>
<html lang="en">
<head>
<meta charset="utf-8">
<title>Hollow Meridian — Dorian Welbeck</title>
<meta name="keywords" content="Hollow Meridian, Conspiracy, Conspiracy Books, Spy books, Thriller books, Suspense books, Comedy books, Dorian Welbeck">
<link rel="stylesheet" href="https://fonts.googleapis.com/css2?family=Playfair+Display:wght@400&family=Arimo:wght@400&display=swap">
<style>
:root{
  --ink:#1e1e1e;
  --muted:#555;
  --header:#2b2a27;
  --footer:#222223;
  --accent:#e07b1a;
  --line:#d6d6d6;
  --white:#fff;
}
*{box-sizing:border-box;margin:0;padding:0}
html,body{width:696px;height:1200px;overflow:hidden;background:var(--white)}
body{position:relative;font-family:"Playfair Display",serif;color:var(--ink)}
.site-header{position:absolute;left:0;top:0;width:696px;height:69px;background:var(--header);border-top:1px solid #6a6658}
.site-title{position:absolute;left:65px;top:24px;font-size:16px;color:var(--white);letter-spacing:.2px;white-space:nowrap}
.menu-button{position:absolute;left:595px;top:17px;width:37px;height:37px;border:1.5px solid var(--white);border-radius:50%}
.menu-button svg{position:absolute;left:12px;top:13px}
.hero{position:absolute;left:0;top:69px;width:696px;height:351px;
  background:linear-gradient(180deg,#3b3a33 0%,#4a4536 22%,#2d2c27 45%,#2a2823 75%,#232320 100%)}
.hero-glow{position:absolute;inset:0;background:radial-gradient(ellipse at 60% 35%,rgba(160,120,60,.25),transparent 55%)}
.play-button{position:absolute;left:323px;top:86px;width:51px;height:51px;border:2px solid var(--white);border-radius:50%;background:#1d1c1a}
.play-button svg{position:absolute;left:18px;top:14px}
.hero-title{position:absolute;left:0;top:146px;width:696px;text-align:center;font-size:27px;color:var(--white)}
.hero-lead{position:absolute;left:140px;top:189px;width:416px;text-align:center;font-size:14.5px;line-height:21px;color:#f2efe8}
.book-card{position:absolute;background:var(--white);border:1px solid #ececec;box-shadow:0 0 3px rgba(0,0,0,.08)}
.book-photo{position:absolute;display:block}
.book-info{position:absolute}
.book-title{font-size:17px;font-weight:400;line-height:22px;white-space:nowrap}
.book-edition{font-size:15px;font-weight:400;line-height:22px;color:var(--muted);white-space:nowrap}
.book-blurb{margin-top:12px;font-family:"Arimo",Arial,sans-serif;font-size:7.9px;line-height:15px;color:#444;text-align:justify}
.store-box{position:absolute;border:1px solid var(--line);border-radius:3px;height:60px;display:block;text-decoration:none;color:var(--ink)}
.store-name{position:absolute;left:0;top:0;height:58px;display:flex;align-items:center;justify-content:center;font-size:19px;color:var(--ink)}
.store-divider{position:absolute;top:12px;width:1px;height:36px;background:var(--line)}
.store-note{position:absolute;top:15px;font-size:10.5px;line-height:15px}
.direct-link{position:absolute;font-size:11px;white-space:nowrap}
.direct-link a{color:var(--accent)}
.site-footer{position:absolute;left:0;top:1151px;width:696px;height:49px;background:var(--footer);color:var(--white);text-align:center;font-size:10.5px;line-height:49px}
</style>
</head>
<body>

<header class="site-header">
  <div class="site-title">HOLLOW MERIDIAN</div>
  <div class="menu-button" aria-label="Menu">
    <svg width="10" height="9" viewBox="0 0 10 9"><rect y="0" width="10" height="1.8" fill="#fff"/><rect y="3.6" width="10" height="1.8" fill="#fff"/><rect y="7.2" width="10" height="1.8" fill="#fff"/></svg>
  </div>
</header>

<section class="hero" role="img" aria-label="Aerial city skyline at dusk, background of the book trailer video">
  <div class="hero-glow"></div>
  <div class="play-button" aria-label="Play trailer">
    <svg width="17" height="20" viewBox="0 0 17 20"><path d="M0 0 L17 10 L0 20 Z" fill="#fff"/></svg>
  </div>
  <h1 class="hero-title" style="font-weight:400">HOLLOW MERIDIAN</h1>
  <p class="hero-lead">Sed ut perspiciatis unde omnis iste natus error sit voluptatem accusantium doloremque laudantium, totam</p>
</section>

<div class="book-card" style="left:76px;top:458px;width:203px;height:307px">
  <a href="https://www.rivermart.example/dp/X00AAAAAA1/?coliid=QWERTYUIOPASD&amp;colid=1ZXCVBNMLKJH0&amp;psc=0&amp;ref_=lv_ov_lig_dp_i" class="book-photo" style="left:10px;top:24px;width:185px;height:275px;background:linear-gradient(160deg,#1b2a5a 0%,#6a1418 35%,#1a1a1a 60%,#0b0b0b 100%)" role="img" aria-label="Hardcover book Hollow Meridian by Dorian Welbeck, flag and portrait cover"></a>
</div>

<div class="book-info" style="left:301px;top:481px;width:307px">
  <h2 class="book-title">HOLLOW MERIDIAN</h2>
  <h3 class="book-edition">PAGEWISP EDITION</h3>
  <p class="book-blurb">A fictional novel based on current events surrounding the covid 19 virous. Jack Holman is a well-respected independent journalist contracted by the Harbor Ledger, upon his return from reporting on the war in Syria he is tasked to investigate the covid virus outbreak in China. As he digs deeper, he uncovers a hideous plot by the powers that be here in America. Jack risks life and limb to uncover the conspirers behind all of this and shed light to the American people.</p>
</div>

<a class="store-box" style="left:299px;top:639px;width:310px" href="https://www.rivermart.example/dp/X00AAAAAA1/?coliid=QWERTYUIOPASD&amp;colid=1ZXCVBNMLKJH0&amp;psc=0&amp;ref_=lv_ov_lig_dp_i">
  <span class="store-name" style="width:139px">Rivermart</span>
  <span class="store-divider" style="left:139px"></span>
  <span class="store-note" style="left:155px;width:145px">Free to new Pagewisp members on Rivermart.com</span>
</a>
<p class="direct-link" style="left:299px;top:714px">Click to go directly to <a href="https://www.rivermart.example/dp/X00AAAAAA1/?coliid=QWERTYUIOPASD&amp;colid=1ZXCVBNMLKJH0&amp;psc=0&amp;ref_=lv_ov_lig_dp_i">Rivermart.com</a></p>

<div class="book-info" style="left:87px;top:836px;width:307px">
  <h2 class="book-title">HOLLOW MERIDIAN</h2>
  <h3 class="book-edition">PAGEWISP EDITION</h3>
  <p class="book-blurb">A fictional novel based on current events surrounding the covid 19 virous. Jack Holman is a well-respected independent journalist contracted by the Harbor Ledger, upon his return from reporting on the war in Syria he is tasked to investigate the covid virus outbreak in China. As he digs deeper, he uncovers a hideous plot by the powers that be here in America. Jack risks life and limb to uncover the conspirers behind all of this and shed light to the American people.</p>
</div>

<a class="store-box" style="left:85px;top:994px;width:310px" href="https://www.listenly.example/pd/Hollow-Meridian-Audiobook/X00BBBBBB2?qid=1000000001&amp;sr=1-7&amp;ref=a_search_c3_lProduct_1_7&amp;pf_rd_p=00000000-aaaa-bbbb-cccc-000000000000&amp;pf_rd_r=ZZZZ00000000000000QQ">
  <span class="store-name" style="width:139px">Listenly</span>
  <span class="store-divider" style="left:139px"></span>
  <span class="store-note" style="left:155px;width:145px">Free to new members of Listenly.com</span>
</a>
<p class="direct-link" style="left:85px;top:1069px">Click to go directly to <a href="https://www.listenly.example/pd/Hollow-Meridian-Audiobook/X00BBBBBB2?qid=1000000001&amp;sr=1-7&amp;ref=a_search_c3_lProduct_1_7&amp;pf_rd_p=00000000-aaaa-bbbb-cccc-000000000000&amp;pf_rd_r=ZZZZ00000000000000QQ">Listenly.com</a></p>

<div class="book-card" style="left:417px;top:813px;width:203px;height:307px">
  <div class="book-photo" style="left:11px;top:9px;width:180px;height:288px;background:linear-gradient(180deg,#050505 0%,#0a0a0a 30%,#2a3560 45%,#7a1a1c 75%,#111 100%)" role="img" aria-label="Audiobook cover of Hollow Meridian by Dorian Welbeck"></div>
</div>

<footer class="site-footer">Hollow Meridian © 2022.All Rights Reserved.</footer>

</body>
</html>
```